Business Card Design Project - del varosi group

dear Sirs

we need business card design for our group ( DEL Varosi Group ) , i have got the Logo design of our group from pixel harbor in previous , so all need details relating to our group i think available with you, as well as the the chosen logo design

we hope to provide us with business card logo that to be appropaite and satisfactory to us .

thanks

note : logo design of our group is attached .
Updates

Reason: please extend the deadline of my project for additional 15 days because i didn't received appropriate design for our gruop yet . kindly beaware that i have received 77 design till now , supossed to send me 200-250 design at least . thanks

Target Market(s)

contents

name : Kerem EL Nadiri

position : Operation Manager

Industry/Entity Type

Business

Requirements
Must have

• person name

group logo
Nice to have
• logo color matching with back background

```html
<!DOCTYPE html>
<html lang="en">
<head>
<meta charset="utf-8">
<title>DEL Varosi Group – Business Card</title>
<link href="https://fonts.googleapis.com/css2?family=Cinzel:wght@600&family=Didact+Gothic&display=swap" rel="stylesheet">
<style>
  :root {
    --page: #eceae6;
    --brand-blue: #1458a6;
    --deep-blue: #0d3f80;
    --gold: #c9a03a;
    --gold-light: #ecd38a;
    --ink: #3b3f45;
    --card-white: #ffffff;
    --card-grey: #e4e4e4;
  }
  * { margin: 0; padding: 0; box-sizing: border-box; }
  html, body { width: 1200px; height: 900px; overflow: hidden; }
  body {
    background: var(--page);
    font-family: "Didact Gothic", "Century Gothic", sans-serif;
    display: flex;
    align-items: center;
    justify-content: center;
    gap: 28px;
  }
  .card {
    position: relative;
    width: 560px;
    height: 320px;
    border-radius: 16px;
    overflow: hidden;
    box-shadow: 0 6px 18px rgba(0,0,0,0.18);
  }
  .card-contact { background: linear-gradient(180deg, var(--card-white) 0%, var(--card-grey) 100%); }
  .card-brand { background: var(--card-white); }
  .card-waves { position: absolute; inset: 0; width: 100%; height: 100%; }

  .wordmark {
    position: absolute;
    display: flex;
    align-items: center;
    gap: 12px;
    color: var(--brand-blue);
    font-weight: 400;
    letter-spacing: 0.5px;
    white-space: nowrap;
  }
  .wordmark-square { background: var(--brand-blue); display: block; }
  .card-contact .wordmark { left: 28px; top: 26px; font-size: 34px; }
  .card-contact .wordmark-square { width: 22px; height: 22px; }
  .card-brand .wordmark { left: 50%; top: 150px; transform: translateX(-50%); font-size: 40px; }
  .card-brand .wordmark-square { width: 26px; height: 26px; }

  .contact-list {
    position: absolute;
    left: 20px; top: 118px;
    list-style: none;
    font-size: 13px;
    color: var(--ink);
    white-space: nowrap;
  }
  .contact-list li { display: flex; align-items: center; gap: 8px; height: 23px; }
  .contact-list.secondary { left: 222px; top: 141px; }
  .icon { width: 15px; height: 15px; flex: none; }

  .person {
    position: absolute;
    right: 38px; bottom: 22px;
    text-align: right;
    color: #fff;
  }
  .person-name { font-family: "Cinzel", "Trajan Pro", serif; font-weight: 600; font-size: 19px; letter-spacing: 0.5px; }
  .person-role { font-size: 14px; color: #f3e6bd; margin-top: 2px; }

  .site-url {
    position: absolute;
    left: 48px; top: 20px;
    color: #fff;
    font-size: 17px;
  }
</style>
</head>
<body>

<svg width="0" height="0" style="position:absolute" aria-hidden="true">
  <defs>
    <linearGradient id="blueBand" x1="0" y1="0" x2="1" y2="0">
      <stop offset="0" stop-color="#0d3f80"/>
      <stop offset="0.5" stop-color="#1a66b8"/>
      <stop offset="1" stop-color="#0d3f80"/>
    </linearGradient>
    <linearGradient id="goldBand" x1="0" y1="0" x2="1" y2="0">
      <stop offset="0" stop-color="#b88a26"/>
      <stop offset="0.5" stop-color="#e8c76a"/>
      <stop offset="1" stop-color="#c9a03a"/>
    </linearGradient>
  </defs>
</svg>

<!-- Contact side -->
<article class="card card-contact">
  <svg class="card-waves" viewBox="0 0 560 320" aria-hidden="true">
    <path d="M0,238 C150,280 300,170 560,192 L560,320 L0,320 Z" fill="url(#goldBand)"/>
    <path d="M0,252 C150,292 300,184 560,204 L560,320 L0,320 Z" fill="#f4e7bf"/>
    <path d="M0,258 C150,298 300,190 560,210 L560,320 L0,320 Z" fill="url(#goldBand)"/>
    <path d="M0,270 C150,310 300,206 560,222 L560,320 L0,320 Z" fill="url(#blueBand)"/>
  </svg>

  <div class="wordmark"><span class="wordmark-square"></span>DEL Varosi Group</div>

  <ul class="contact-list">
    <li>
      <svg class="icon" viewBox="0 0 16 16"><circle cx="8" cy="8" r="8" fill="var(--brand-blue)"/><path d="M8,3.5 L12.5,7.5 H11 V12 H9 V9.5 H7 V12 H5 V7.5 H3.5 Z" fill="#fff"/></svg>
      P.O. Box: 48210, Westmere Bay Harbor District
    </li>
    <li>
      <svg class="icon" viewBox="0 0 16 16"><circle cx="8" cy="8" r="8" fill="var(--brand-blue)"/><path d="M3.5,7 Q8,3 12.5,7 L11,8.5 L9.5,7.3 H6.5 L5,8.5 Z M5,9 H11 V12 H5 Z" fill="#fff"/></svg>
      (555) 214-3087
    </li>
    <li>
      <svg class="icon" viewBox="0 0 16 16"><circle cx="8" cy="8" r="8" fill="var(--brand-blue)"/><rect x="4" y="5" width="8" height="6" fill="#fff"/><path d="M4,5 L8,8.5 L12,5" stroke="var(--brand-blue)" fill="none"/></svg>
      info@delvarosi.com
    </li>
    <li>
      <svg class="icon" viewBox="0 0 16 16"><circle cx="8" cy="8" r="8" fill="var(--brand-blue)"/><circle cx="8" cy="8" r="4.5" fill="none" stroke="#fff"/><ellipse cx="8" cy="8" rx="2" ry="4.5" fill="none" stroke="#fff"/><line x1="3.5" y1="8" x2="12.5" y2="8" stroke="#fff"/></svg>
      www.delvarosi.com
    </li>
  </ul>

  <ul class="contact-list secondary">
    <li>
      <svg class="icon" viewBox="0 0 16 16"><circle cx="8" cy="8" r="8" fill="var(--brand-blue)"/><rect x="5.5" y="3.5" width="5" height="9" rx="1" fill="#fff"/><rect x="6.5" y="5" width="3" height="4.5" fill="var(--brand-blue)"/></svg>
      (555) 214-3090
    </li>
    <li>
      <svg class="icon" viewBox="0 0 16 16"><circle cx="8" cy="8" r="8" fill="var(--brand-blue)"/><rect x="4" y="6" width="8" height="6" fill="#fff"/><rect x="5.5" y="3.5" width="5" height="3" fill="#fff"/><rect x="6" y="8" width="4" height="2" fill="var(--brand-blue)"/></svg>
      (555) 214-3095
    </li>
  </ul>

  <div class="person">
    <div class="person-name">Kerem EL Nadiri</div>
    <div class="person-role">Operation Manager</div>
  </div>
</article>

<!-- Brand side -->
<article class="card card-brand">
  <svg class="card-waves" viewBox="0 0 560 320" aria-hidden="true">
    <path d="M0,0 H560 V82 C400,52 330,118 160,112 C90,110 40,100 0,92 Z" fill="url(#goldBand)"/>
    <path d="M0,0 H560 V70 C400,40 330,104 160,98 C90,96 40,88 0,80 Z" fill="#f4e7bf"/>
    <path d="M0,0 H560 V64 C400,34 330,98 160,92 C90,90 40,82 0,74 Z" fill="url(#goldBand)"/>
    <path d="M0,0 H560 V50 C400,24 330,84 160,78 C90,76 40,68 0,60 Z" fill="url(#blueBand)"/>
  </svg>

  <div class="site-url">www.delvarosi.com</div>

  <div class="wordmark"><span class="wordmark-square"></span>DEL Varosi Group</div>
</article>

</body>
</html>
```